Animal Horse & Bedding Company Needs a Website Coded & Designed

We need a website for a new animal bedding and feed company that is visually grabbing and vibrant. We would like to see a website that displays trust, quality and confidence. Needs to be responsive and mobile friendly for all browsers and coded for both Android & IOS. SEO is also important.

Joomla or Wordpress – must be both desktop and mobile friendly with fast page load speed. Need the ability to edit ourselves in Wordpress or Joomla.

Full details attached below with some layout and content ideas.

Coding

Coded - Design and coding required

Number of Pages Required

5+ page

Font styles to use
Sans Serif

Requirements
Must have
• Needs to be responsive and mobile friendly for all browsers and coded for both Android & IOS. SEO is also important.

Wordpress – must be both desktop and mobile friendly with fast page load speed. Need the ability to edit ourselves in Wordpress.

Logo Colours:
Dark Brown
CMYK: 50 / 70 / 80 / 70
Pantone: 4625C

Orange
CMYK: 0 / 50 / 100 / 0
Pantone: 144C
Nice to have
• Use picture of building attached and super impose logo on building.

```html
<!DOCTYPE html>
<html lang="en">
<head>
<meta charset="utf-8">
<title>Golden Sheaf – Bedding &amp; Feed</title>
<link rel="stylesheet" href="https://fonts.googleapis.com/css2?family=Pathway+Gothic+One&family=Poppins:wght@400;500;600&family=Montserrat:wght@400;500&display=swap">
<style>
:root{
  --brown:#3d2516;
  --brown-deep:#33200f;
  --orange:#f7931e;
  --white:#ffffff;
  --ink:#2b2b2b;
  --muted:#8a8a8a;
  --line:#3d2516;
  --hero-top:#c9b58a;
  --hero-bottom:#b9a24e;
  --emblem:#c9a27a;
  --pasture-top:#8fa36a;
  --pasture-bottom:#5f9e34;
}
*{box-sizing:border-box;margin:0;padding:0}
html,body{width:1200px;height:2950px;overflow:hidden;background:var(--white)}
body{font-family:"Poppins",sans-serif;color:var(--ink);position:relative}
.page{position:absolute;left:71px;top:114px;width:1057px;height:2749px;background:var(--white);box-shadow:0 10px 40px rgba(0,0,0,.25);overflow:hidden}
.abs{position:absolute}
.display{font-family:"Pathway Gothic One",sans-serif;font-weight:400;letter-spacing:.02em}

/* header */
.topbar{left:0;top:0;width:100%;height:88px;background:var(--brown)}
.contact-line{left:66px;font-size:11px;color:var(--white);display:flex;align-items:center;gap:14px}
.contact-line svg{width:14px;height:14px;fill:var(--orange)}
.brand{left:0;width:100%;top:22px;text-align:center;font-size:30px;color:var(--white)}
.search{left:763px;top:32px;width:237px;height:26px;background:var(--white);border-radius:3px;font-size:10px;color:#b3b3b3;padding:6px 14px;display:flex;justify-content:space-between;align-items:center}
.search svg{width:10px;height:10px;stroke:var(--orange);fill:none;stroke-width:2}
.nav{left:0;top:88px;width:100%;height:31px;background:var(--orange)}
.nav a{position:absolute;top:7px;transform:translateX(-50%);font-size:13px;color:var(--white);text-decoration:none;white-space:nowrap}

/* hero */
.hero{left:0;top:119px;width:100%;height:521px;background:linear-gradient(180deg,var(--hero-top) 0%,var(--hero-bottom) 100%)}
.hero-kicker{left:83px;top:234px;font-size:34px;color:var(--white)}
.hero-title{left:83px;top:268px;font-size:88px;line-height:1;color:var(--white)}
.hero-sub{left:83px;top:377px;font-size:50px;color:var(--white);letter-spacing:.06em}
.btn{display:inline-block;background:var(--orange);color:var(--white);font-size:15px;text-align:center;border-radius:2px;box-shadow:0 3px 6px rgba(0,0,0,.2);letter-spacing:.06em}

/* sections */
.title{font-size:44px;color:var(--brown);line-height:1}
.rule{height:4px;width:69px;background:var(--brown)}
.para{font-size:12.3px;line-height:18.3px;color:#222}
.list{list-style:none;font-family:"Montserrat",sans-serif;font-size:11.3px;line-height:17.6px;color:#222;letter-spacing:.03em}
.list li::before{content:"• "}
.photo{background:linear-gradient(180deg,var(--pasture-top) 0%,var(--pasture-bottom) 100%)}

/* quote */
.info-label{font-size:22px;color:var(--brown)}
.info-text{font-family:"Montserrat",sans-serif;font-size:15.5px;line-height:20px;color:#222;letter-spacing:.02em}
.info-icon{width:34px;height:34px;fill:var(--orange)}
.field{border-bottom:1.5px solid var(--line);font-family:"Montserrat",sans-serif;font-size:13.5px;color:var(--muted);padding:0 6px 10px}
.send{background:var(--brown);color:var(--white);font-size:20px;text-align:center;padding-top:6px}

/* newsletter + footer */
.footer{left:0;top:2436px;width:100%;height:313px;background:var(--brown-deep)}
.newsletter{left:120px;top:2382px;width:815px;height:80px;background:var(--orange)}
.newsletter .label{left:30px;top:26px;font-size:24px;color:var(--brown)}
.newsletter .input{left:280px;top:24px;width:360px;height:32px;background:var(--white);font-size:11.5px;color:#9a9a9a;padding:9px 14px}
.newsletter .submit{left:655px;top:24px;width:143px;height:32px;background:var(--brown);color:var(--white);font-size:19px;text-align:center;padding-top:4px}
.f-brand{left:146px;top:2540px;font-size:30px;color:var(--white)}
.f-text{left:143px;top:2596px;width:200px;font-size:11.5px;line-height:16.4px;color:#e8e0d8;letter-spacing:.05em}
.f-head{font-size:17.5px;font-weight:500;color:var(--white);padding-bottom:2px;border-bottom:2px solid var(--orange);display:inline-block;line-height:1.2}
.f-col{font-size:11.5px;font-weight:600;color:var(--white);letter-spacing:.04em}
.f-social{font-size:11px;color:var(--white);display:flex;align-items:center;gap:16px;letter-spacing:.04em}
.f-social i{display:inline-block;width:11px;height:11px;border:1.5px solid var(--white);border-radius:50%}
.f-rule{left:120px;top:2710px;width:815px;height:1px;background:#7a6757}
.copyright{left:0;width:100%;top:2722px;text-align:center;font-size:11.5px;color:var(--white)}
</style>
</head>
<body>
<div class="page">

  <header>
    <div class="abs topbar"></div>
    <div class="abs contact-line" style="top:26px">
      <svg viewBox="0 0 24 24"><path d="M6.6 10.8a15.1 15.1 0 0 0 6.6 6.6l2.2-2.2c.3-.3.7-.4 1-.2 1.1.4 2.3.6 3.6.6.6 0 1 .4 1 1V20c0 .6-.4 1-1 1A17 17 0 0 1 3 4c0-.6.4-1 1-1h3.5c.6 0 1 .4 1 1 0 1.3.2 2.5.6 3.6.1.3 0 .7-.2 1z"/></svg>
      <span>0800-555-0142</span>
    </div>
    <div class="abs contact-line" style="top:48px">
      <svg viewBox="0 0 24 24"><path d="M2 5h20v2l-10 6L2 7z M2 9l10 6 10-6v10H2z"/></svg>
      <span>hello@goldensheaf.example</span>
    </div>
    <div class="abs brand display">GOLDEN SHEAF</div>
    <div class="abs search"><span>Search</span><svg viewBox="0 0 12 12"><circle cx="5" cy="5" r="3.5"/><path d="M8 8l3 3"/></svg></div>
    <nav class="abs nav">
      <a style="left:254px">Home</a>
      <a style="left:343px">About</a>
      <a style="left:429px">Feed</a>
      <a style="left:522px">Bedding</a>
      <a style="left:637px">Contact Us</a>
      <a style="left:773px">Requets Quote</a>
    </nav>
  </header>

  <section class="hero-block">
    <div class="abs hero" role="img" aria-label="Photo of a chestnut horse standing in a sunlit grassy meadow"></div>
    <div class="abs hero-kicker display">WELLCOME</div>
    <h1 class="abs hero-title display">GOLDEN SHEAF</h1>
    <div class="abs hero-sub display">BEDDING &amp; FEED</div>
    <a class="abs btn display" style="left:83px;top:444px;width:117px;height:28px;padding-top:5px">SHOP NOW</a>
  </section>

  <section class="about">
    <div class="abs" style="left:139px;top:699px;width:220px;height:307px;background:var(--emblem)" role="img" aria-label="Brand emblem illustration"></div>
    <h2 class="abs title display" style="left:506px;top:724px">ABOUT US</h2>
    <div class="abs rule" style="left:506px;top:774px"></div>
    <p class="abs para" style="left:506px;top:799px;width:432px">Looking for the best bedding and feed for your horse, livestock or household pet look no further.&nbsp; We use premium locally sourced straw and hay in all of our products and are committed in providing quality products and service.<br>Your animal deserves the very best in health and comfort to keep them healthy, strong and happy.&nbsp; Our products are designed for horses, livestock (goats, cattle and sheep), small caged animals (rabbits, guinea pigs and more).</p>
    <a class="abs btn display" style="left:506px;top:968px;width:117px;height:29px;padding-top:5px">LEARN MORE</a>
  </section>

  <section class="bedding">
    <h2 class="abs title display" style="left:91px;top:1128px">BEDDING BENEFIT</h2>
    <div class="abs rule" style="left:91px;top:1178px"></div>
    <ul class="abs list" style="left:91px;top:1207px">
      <li>100% Natural Chopped Straw</li>
      <li>Low Dust</li>
      <li>Chemical &amp; Additive Free</li>
      <li>Clean &amp; Highly Absorbent</li>
      <li>Cheaper than Wood Shavings</li>
      <li>Economic – less used and less wasted</li>
      <li>Environmentally Friendly – Recyclable &amp; Compostable</li>
    </ul>
    <a class="abs btn display" style="left:91px;top:1358px;width:117px;height:28px;padding-top:5px">SHOP NOW</a>
    <div class="abs photo" style="left:513px;top:1095px;width:440px;height:348px" role="img" aria-label="Photo of a young foal in a green paddock"></div>
  </section>

  <section class="feed">
    <div class="abs photo" style="left:87px;top:1444px;width:426px;height:379px" role="img" aria-label="Photo of a bay horse grazing on a green pasture"></div>
    <h2 class="abs title display" style="left:576px;top:1499px">FEED BENEFIT</h2>
    <div class="abs rule" style="left:576px;top:1549px"></div>
    <ul class="abs list" style="left:576px;top:1579px">
      <li>100% Natural</li>
      <li>Chemical &amp; Additive Free</li>
      <li>Available in Pellets or Cubes</li>
      <li>High Protein Content</li>
      <li>Eliminate Waste In Feeding</li>
      <li>Clean - Eliminates Dust From Feeding Baled Hay</li>
      <li>Cost Effective</li>
      <li>Convenient</li>
      <li>Less wasted feed</li>
    </ul>
    <a class="abs btn display" style="left:576px;top:1765px;width:117px;height:28px;padding-top:5px">SHOP NOW</a>
  </section>

  <section class="quote">
    <h2 class="abs title display" style="left:113px;top:1905px;font-size:54px;letter-spacing:.05em">REQUEST A QUOTE</h2>
    <div class="abs rule" style="left:113px;top:1970px;width:60px"></div>

    <svg class="abs info-icon" style="left:113px;top:2030px" viewBox="0 0 24 24"><path d="M21 3 3 10.5l7.5 2.5L13 21z"/></svg>
    <div class="abs info-label display" style="left:166px;top:2030px">LOCATION</div>
    <div class="abs info-text" style="left:166px;top:2060px">48 Meadow Lane, Fairfield,<br>NY 10101 North America</div>

    <svg class="abs info-icon" style="left:113px;top:2137px" viewBox="0 0 24 24"><path d="M2 5h20v2.5l-10 6-10-6z M2 10l10 6 10-6v9H2z"/></svg>
    <div class="abs info-label display" style="left:166px;top:2137px">EMAIL</div>
    <div class="abs info-text" style="left:166px;top:2165px">info@goldensheaf.example</div>

    <svg class="abs info-icon" style="left:113px;top:2220px" viewBox="0 0 24 24"><path d="M6.6 10.8a15.1 15.1 0 0 0 6.6 6.6l2.2-2.2c.3-.3.7-.4 1-.2 1.1.4 2.3.6 3.6.6.6 0 1 .4 1 1V20c0 .6-.4 1-1 1A17 17 0 0 1 3 4c0-.6.4-1 1-1h3.5c.6 0 1 .4 1 1 0 1.3.2 2.5.6 3.6.1.3 0 .7-.2 1z"/></svg>
    <div class="abs info-label display" style="left:166px;top:2221px">PHONE</div>
    <div class="abs info-text" style="left:166px;top:2250px">+1 020 555 0198</div>

    <form>
      <div class="abs field" style="left:441px;top:2037px;width:244px;height:28px">Name</div>
      <div class="abs field" style="left:703px;top:2037px;width:243px;height:28px">Email</div>
      <div class="abs field" style="left:441px;top:2097px;width:244px;height:28px">Subject</div>
      <div class="abs field" style="left:703px;top:2097px;width:243px;height:28px;display:flex;justify-content:space-between">Country
        <svg width="12" height="12" viewBox="0 0 12 12" style="margin-top:3px"><path d="M2 4l4 4 4-4" stroke="#222" stroke-width="2" fill="none"/></svg></div>
      <div class="abs field" style="left:441px;top:2157px;width:505px;height:55px">Message or Comment</div>
      <div class="abs send display" style="left:447px;top:2241px;width:97px;height:36px">SEND</div>
    </form>
  </section>

  <footer>
    <div class="abs footer"></div>
    <div class="abs newsletter">
      <div class="abs label display">SUBSCRIBE FOR NEWSLETTER</div>
      <div class="abs input">Your Email Address</div>
      <div class="abs submit display">SUBSCRIBE</div>
    </div>

    <div class="abs f-brand display">GOLDEN SHEAF</div>
    <p class="abs f-text">Golden Sheaf offers supply and delivery of fresh bedding as well as removal of waste bedding.</p>

    <div class="abs" style="left:407px;top:2508px"><span class="f-head">Get in touch</span></div>
    <div class="abs f-col" style="left:409px;top:2561px">0811-555-0101</div>
    <div class="abs f-col" style="left:409px;top:2600px">022-555-0177</div>
    <div class="abs f-col" style="left:409px;top:2639px">0811-555-0123</div>

    <div class="abs" style="left:594px;top:2508px"><span class="f-head">Useful Links</span></div>
    <div class="abs f-col" style="left:595px;top:2558px;line-height:18.9px;font-size:11px">Home<br>About<br>Feed<br>Bedding<br>Contact Us<br>Request Quote</div>

    <div class="abs" style="left:781px;top:2508px"><span class="f-head">Connect</span></div>
    <div class="abs f-social" style="left:784px;top:2561px"><i></i>Photos</div>
    <div class="abs f-social" style="left:784px;top:2587px"><i></i>Community</div>
    <div class="abs f-social" style="left:784px;top:2612px"><i></i>Updates</div>
    <div class="abs f-social" style="left:784px;top:2637px"><i></i>Videos</div>

    <div class="abs f-rule"></div>
    <div class="abs copyright">© Copyright 2020 Golden Sheaf. All Rights Reserved.</div>
  </footer>

</div>
</body>
</html>
```